Weightloss company needs Business Card

We want a business card that is clean and professional, yet portrays that we are a friendly, innovative, and versatile program designed to fit the needs of our clients.
I would like there to be 2 sides, one side having an appointment card, and the other side containing the logo and business information. There can be decorations on both sides. The logo is attached.

Target Market(s)

Men and women 40-60

Industry/Entity Type

Business

Contact Information for Business Card

Font styles to use
Sans Serif

Requirements
Must have
• The logo, space for business information
Nice to have
• The colors in the logo
Should not have
• No pictures of people or food

```html
<!DOCTYPE html>
<html lang="en">
<head>
<meta charset="utf-8">
<title>Renewal Wellness – Business Card</title>
<link href="https://fonts.googleapis.com/css2?family=Open+Sans:ital,wght@0,400;0,600;1,400&display=swap" rel="stylesheet">
<style>
  :root {
    --brand-red: #d3112f;
    --accent-cyan: #29b6d9;
    --text-grey: #505050;
    --muted-grey: #5c5c5c;
    --card-bg: #f6f6f6;
    --page-bg: #e4e4e4;
  }
  * { margin: 0; padding: 0; box-sizing: border-box; }
  html, body { width: 1105px; height: 1200px; overflow: hidden; }
  body {
    background: var(--page-bg);
    font-family: "Open Sans", Arial, sans-serif;
    position: relative;
  }
  .card {
    position: absolute;
    left: 102px;
    width: 900px;
    height: 514px;
    background: var(--card-bg);
    overflow: hidden;
  }
  .card--front { top: 50px; }
  .card--back { top: 636px; }
  .abs { position: absolute; white-space: nowrap; }

  /* Front */
  .brand-band {
    position: absolute; left: 779px; top: 57px; width: 121px; height: 140px;
    background: var(--brand-red);
  }
  .brand-name {
    right: 142px; top: 90px;
    font-size: 32px; line-height: 36px; font-weight: 600; color: var(--brand-red);
    text-align: right;
  }
  .person-name {
    left: 42px; top: 296px;
    font-size: 31px; font-weight: 600; color: var(--brand-red); letter-spacing: 0.5px;
  }
  .person-role {
    left: 42px; top: 348px;
    font-size: 23px; color: var(--accent-cyan);
  }
  .role-rule {
    position: absolute; left: 224px; top: 366px; width: 625px; height: 2px;
    background: var(--accent-cyan);
  }
  .contact { font-size: 23px; color: var(--text-grey); line-height: 33px; }
  .address { left: 44px; top: 410px; }
  .contact-list { top: 410px; }
  .contact-list li { list-style: none; display: flex; align-items: center; gap: 14px; height: 33px; }
  .contact-list svg { width: 22px; height: 22px; fill: var(--brand-red); flex: none; }
  .phones { left: 350px; }
  .online { left: 570px; }

  /* Back */
  .appt-title {
    left: 0; width: 900px; top: 50px; text-align: center;
    font-size: 33px; font-weight: 600; color: var(--brand-red);
  }
  .dotted { position: absolute; border-bottom: 2px dotted #8a8a8a; height: 0; }
  .field-label { font-size: 23px; color: var(--brand-red); }
  .body-text { font-size: 23px; color: var(--text-grey); }
  .ampm { font-size: 18px; color: var(--brand-red); }
  .day { font-size: 22px; color: var(--brand-red); top: 334px; }
  .tick-box {
    position: absolute; top: 336px; width: 25px; height: 25px;
    border: 2px solid #555;
  }
  .notice {
    left: 0; width: 900px; top: 430px; text-align: center;
    font-size: 18px; font-style: italic; color: var(--muted-grey); line-height: 26px;
  }
</style>
</head>
<body>

<section class="card card--front" aria-label="Business card front">
  <div class="brand-band"></div>
  <div class="abs brand-name">Renewal<br>Wellness</div>

  <div class="abs person-name">DANIEL CARVER</div>
  <div class="abs person-role">CEO/FOUNDER</div>
  <div class="role-rule"></div>

  <div class="abs contact address">4120 Birchwood Drive<br>Fairbanks, Alaska 99701</div>

  <ul class="abs contact contact-list phones">
    <li>
      <svg viewBox="0 0 24 24" aria-hidden="true"><path d="M6.6 10.8a15.1 15.1 0 0 0 6.6 6.6l2.2-2.2c.3-.3.7-.4 1-.2 1.1.4 2.3.6 3.6.6.6 0 1 .4 1 1V20c0 .6-.4 1-1 1A17 17 0 0 1 3 4c0-.6.4-1 1-1h3.5c.6 0 1 .4 1 1 0 1.3.2 2.5.6 3.6.1.3 0 .7-.2 1z"/></svg>
      555 214 7830
    </li>
    <li>
      <svg viewBox="0 0 24 24" aria-hidden="true"><path d="M7 1h10a2 2 0 0 1 2 2v18a2 2 0 0 1-2 2H7a2 2 0 0 1-2-2V3a2 2 0 0 1 2-2zm0 3v14h10V4zm5 15.5a1.2 1.2 0 1 0 0 2.4 1.2 1.2 0 0 0 0-2.4z"/></svg>
      555 309 6142
    </li>
  </ul>

  <ul class="abs contact contact-list online">
    <li>
      <svg viewBox="0 0 24 24" aria-hidden="true"><path d="M3 5h18v14H3zm2 2v.5l7 5 7-5V7zm0 3v7h14v-7l-7 5z"/></svg>
      hello@renewalwell.com
    </li>
    <li>
      <svg viewBox="0 0 24 24" aria-hidden="true"><circle cx="12" cy="12" r="10"/><path d="M2 12h20M12 2c3 3 3 17 0 20M12 2c-3 3-3 17 0 20" stroke="#f6f6f6" stroke-width="1.6" fill="none"/></svg>
      www.renewalwell.com
    </li>
  </ul>
</section>

<section class="card card--back" aria-label="Appointment card">
  <div class="abs appt-title">Next Appointment</div>

  <div class="dotted" style="left:62px; top:168px; width:524px;"></div>
  <div class="abs body-text" style="left:596px; top:144px;">has an apppointment</div>

  <div class="abs field-label" style="left:50px; top:236px;">Date :</div>
  <div class="dotted" style="left:138px; top:264px; width:340px;"></div>
  <div class="abs field-label" style="left:506px; top:236px;">Time :</div>
  <div class="dotted" style="left:582px; top:264px; width:175px;"></div>
  <div class="abs ampm" style="left:767px; top:242px;">AM/PM</div>

  <div class="abs day" style="left:57px;">Sun</div><div class="tick-box" style="left:111px;"></div>
  <div class="abs day" style="left:171px;">Mon</div><div class="tick-box" style="left:230px;"></div>
  <div class="abs day" style="left:294px;">Tue</div><div class="tick-box" style="left:346px;"></div>
  <div class="abs day" style="left:423px;">Wed</div><div class="tick-box" style="left:478px;"></div>
  <div class="abs day" style="left:544px;">Thu</div><div class="tick-box" style="left:591px;"></div>
  <div class="abs day" style="left:669px;">Fri</div><div class="tick-box" style="left:701px;"></div>
  <div class="abs day" style="left:765px;">Sat</div><div class="tick-box" style="left:804px;"></div>

  <p class="abs notice">Please give me 24 hours notice if you are unable to keep your appointment or<br>a cancellation fee may be charged.</p>
</section>

</body>
</html>
```